Financial & Tax Strategies

need to get a word press site with existing domains and condense existing content on existing site, make new site dynamic, need mobile too......need to take info from my quorvia website and get modern, relevant site, less verbose on first page, way more things to click and engage people. Would like it to look like this , but with my color scheme and not quite as busy looking. I like much of the content on my tabs. Want maximize by seo capabilities on their as well. The number one thing I can say is to go to my existing website and get content, logo, etc there … www.pinegatelarkgroup.com .

Target Market(s)

Those 40 -65, business owners for at least 5 years. Higher net worth.

Number of Pages Required

5+ page

Font styles to use
Sans Serif

Colors
f04a50
e4daeb
ffffff

Requirements
Must have
• seo maximized, lots of places to click on to contact us, calls to action, relevant, conservative, want it to look like this and have the function as well.....slight variation on messaging, but like the simplicity on first view. https://www.dorrickvale.com/
Nice to have
• Some area along right side where videos we do will be.
Should not have
• feel too busy, but still have lots of opportunities to engage.

```html
<!DOCTYPE html>
<html lang="en">
<head>
<meta charset="utf-8">
<title>401ks May Not Be What You Think | Pinegate Lark Group</title>
<link href="https://fonts.googleapis.com/css2?family=Montserrat:wght@400;600;700&family=Open+Sans:wght@400;600;700&display=swap" rel="stylesheet">
<style>
:root{
  --red:#e53238;
  --ink:#2b2b2b;
  --text:#555;
  --muted:#888;
  --line:#e2e2e2;
  --soft:#f5f5f5;
  --footer:#2d2d2d;
  --footer-deep:#232323;
  --white:#fff;
}
*{box-sizing:border-box;margin:0;padding:0}
html,body{width:1200px;height:5143px;overflow:hidden;background:var(--white)}
body{font-family:"Open Sans",Arial,sans-serif;color:var(--text);font-size:12px;line-height:1.55}
h1,h2,h3,h4{font-family:"Montserrat",Arial,sans-serif;color:var(--ink)}
.wrap{width:1060px;margin:0 auto}

.site-header{height:100px;display:flex;align-items:center}
.site-header .wrap{display:flex;justify-content:space-between;align-items:center}
.brand{display:flex;align-items:center;gap:12px}
.brand-dot{width:44px;height:44px;border-radius:50%;background:var(--red)}
.brand-name{font-family:"Montserrat",sans-serif;font-weight:700;font-size:19px;line-height:1.1;color:var(--ink);width:130px}
.header-call{display:flex;align-items:center;gap:10px}
.header-call .icon{width:38px;height:38px;border-radius:50%;background:var(--red);display:flex;align-items:center;justify-content:center}
.header-call p{font-size:12px;line-height:1.35;color:var(--ink)}
.header-call strong{color:var(--red)}

.hero{height:450px;background:linear-gradient(135deg,#c9c4bd 0%,#8f8a83 45%,#5c5a57 100%);display:flex;align-items:center;justify-content:center}
.hero-title{background:rgba(40,40,40,.55);padding:48px 90px}
.hero-title h1{color:var(--white);font-size:30px;font-weight:600}

.intro{height:300px;padding-top:50px}
.intro .wrap{display:flex;gap:40px}
.intro p{flex:1;font-size:12.5px}
.intro-photo{width:420px;height:200px;background:linear-gradient(135deg,#d8d4cf,#6e6a66)}

.myths{height:1300px;padding-top:90px}
.myth{display:flex;gap:14px;margin-bottom:34px}
.myth .mark{width:10px;height:10px;background:var(--red);margin-top:4px;flex:none}
.myth h3{font-size:13px;font-weight:700;margin-bottom:4px}
.myth p{font-size:12px}

.suggest{height:150px;text-align:center;padding-top:30px}
.suggest p{font-family:"Montserrat",sans-serif;font-size:22px;font-weight:600;color:var(--ink);line-height:1.45}

.contact-band{height:230px;background:var(--red);color:var(--white);text-align:center;padding-top:48px}
.contact-band h2{color:var(--white);font-size:32px;font-weight:700}
.contact-lines{display:flex;justify-content:center;gap:50px;margin-top:16px;font-family:"Montserrat",sans-serif;font-size:30px;font-weight:700}
.contact-lines span{display:flex;align-items:center;gap:10px}
.contact-band p{margin-top:12px;font-size:15px}

.strategies{height:450px;padding-top:80px;text-align:center}
.section-title{font-size:32px;font-weight:400;margin-bottom:40px}
.strategy-grid{display:flex;justify-content:center;gap:20px}
.strategy{width:220px;height:200px;background:var(--soft);border:1px solid var(--line);display:flex;flex-direction:column;align-items:center;justify-content:center;gap:18px;padding:0 24px}
.strategy h4{font-size:14px;font-weight:600;line-height:1.35}
.strategy.featured{background:var(--red)}
.strategy.featured h4{color:var(--white)}

.media{height:640px;padding-top:40px;text-align:center}
.media-grid{display:flex;justify-content:center;gap:24px}
.media-card{width:300px;text-align:left;border:1px solid var(--line);background:var(--white)}
.media-card .thumb{height:190px}
.media-card .body{padding:18px 20px 22px}
.media-card h4{font-size:14px;margin-bottom:8px}
.media-card p{font-size:11.5px;margin-bottom:14px}
.more{font-size:11px;color:var(--ink);font-weight:600}
.btn{display:inline-block;background:var(--red);color:var(--white);font-weight:600;font-size:13px;padding:12px 48px;margin-top:40px}

.testimonials{height:620px;padding-top:40px;text-align:center}
.quote-grid{display:flex;justify-content:center;gap:24px}
.quote{width:300px;border:1px solid var(--line);padding:30px 24px 26px}
.avatar{width:90px;height:90px;border-radius:50%;margin:0 auto 16px;background:linear-gradient(135deg,#c9c3bc,#7b756f)}
.quote h4{font-size:14px}
.quote .role{font-size:11px;color:var(--red);margin-bottom:10px;display:block}
.quote p{font-size:11.5px}
.subscribe{display:flex;justify-content:center;margin-top:40px}
.subscribe .field{width:360px;height:36px;border:1px solid var(--line);font-size:12px;color:var(--muted);padding:9px 14px;text-align:left}
.subscribe .go{width:110px;height:36px;background:var(--red);color:var(--white);font-weight:600;font-size:13px;padding-top:8px}

.site-footer{height:903px;background:var(--footer);color:#bdbdbd;padding-top:80px;position:relative}
.footer-grid{display:flex;gap:50px}
.footer-col h4{color:var(--white);font-size:15px;margin-bottom:16px}
.footer-about{width:260px}
.footer-about .brand-name{color:var(--white)}
.footer-about p{margin-top:18px;font-size:12px}
.links{width:140px;list-style:none}
.links li{margin-bottom:8px;font-size:12px}
.links li::before{content:"› ";color:var(--red)}
.address{width:240px;list-style:none}
.address li{display:flex;gap:10px;margin-bottom:10px;font-size:12px;align-items:flex-start}
.footer-form{width:290px}
.row{display:flex;gap:8px;margin-bottom:8px}
.row span{flex:1;height:30px;background:#3a3a3a;font-size:11px;padding:6px 10px;color:#999}
.msg{height:80px;background:#3a3a3a;font-size:11px;padding:6px 10px;color:#999}
.footer-btn{display:inline-block;margin-top:12px;background:var(--red);color:var(--white);font-size:12px;font-weight:600;padding:8px 20px}
.copyright{position:absolute;left:0;right:0;bottom:0;height:54px;background:var(--footer-deep)}
.copyright .wrap{display:flex;justify-content:space-between;align-items:center;height:54px;font-size:11px}
</style>
</head>
<body>

<header class="site-header">
  <div class="wrap">
    <div class="brand"><span class="brand-dot"></span><span class="brand-name">Pinegate Lark Group</span></div>
    <div class="header-call">
      <span class="icon"><svg width="18" height="18" viewBox="0 0 24 24"><path fill="#fff" d="M6.6 10.8a15 15 0 0 0 6.6 6.6l2.2-2.2c.3-.3.7-.4 1-.2 1.1.4 2.3.6 3.6.6.6 0 1 .4 1 1V20c0 .6-.4 1-1 1A17 17 0 0 1 3 4c0-.6.4-1 1-1h3.5c.6 0 1 .4 1 1 0 1.3.2 2.5.6 3.6.1.3 0 .7-.2 1z"/></svg></span>
      <p>Confidential Financial<br>Review <strong>Call Here</strong><br>916.555.0142</p>
    </div>
  </div>
</header>

<section class="hero" role="img" aria-label="Desk with a tablet showing financial charts">
  <div class="hero-title"><h1>401ks May Not Be What You Think</h1></div>
</section>

<section class="intro">
  <div class="wrap">
    <p>We are the only country in the world that has a 401k. Why? Did you know that the "invention" of 401ks in the early 80s was a solution to the slaughter of pensions? Wall Street and the government sold it as a way to give savers control. But the plans shift every risk onto you. Fees are hidden, rules change, and market losses land right when you need the money most. Before you trust your future to a plan built for someone else's benefit, learn how these accounts really work, what they cost you over decades, and which better options are open to business owners like you.</p>
    <div class="intro-photo" role="img" aria-label="Retirement savings jar with coins"></div>
  </div>
</section>

<section class="myths">
  <div class="wrap">
    <div class="myth"><span class="mark"></span><div><h3>You can be wiped out overnight.</h3><p>A market drop can erase years of savings in days. Many savers near retirement lost close to half their 401k value in past crashes and waited a decade to recover, time that people in their sixties simply do not have.</p></div></div>
    <div class="myth"><span class="mark"></span><div><h3>Administrative fees and the tyranny of compounding costs.</h3><p>Fees of one or two percent look small, yet compounded over thirty years they can consume a third of your balance. Fund costs, record keeping charges and trading fees are rarely shown clearly on your statement.</p></div></div>
    <div class="myth"><span class="mark"></span><div><h3>There's no cash flow for better opportunities.</h3><p>Money locked in a 401k cannot be used to buy property, grow your business or seize a good deal. Every dollar sits idle on the sidelines while penalties stand guard over your own savings.</p></div></div>
    <div class="myth"><span class="mark"></span><div><h3>Lack of liquidity when you need it most.</h3><p>Early withdrawals trigger penalties and income tax. Loans must be repaid on a strict schedule, and leaving your job can make the balance due at once. Your money is there, but out of reach.</p></div></div>
    <div class="myth"><span class="mark"></span><div><h3>Lack of knowledge encourages unconscious investing.</h3><p>Most savers pick funds from a short menu and never look again. Few know what they own, what it costs or how it performs, so decisions are left to default settings and chance.</p></div></div>
    <div class="myth"><span class="mark"></span><div><h3>Fear of taxes leads to underutilization.</h3><p>Because every withdrawal is taxed, retirees often spend too little and live below their means. Savings meant for comfort end up passed on with a heavy tax bill attached for heirs.</p></div></div>
    <div class="myth"><span class="mark"></span><div><h3>Higher tax brackets upon withdrawal.</h3><p>The promise was lower taxes in retirement. With fewer deductions and rising rates, many retirees find themselves in the same or a higher bracket when they finally take their money out.</p></div></div>
    <div class="myth"><span class="mark"></span><div><h3>No exit strategy.</h3><p>Required minimum distributions force withdrawals whether you need the money or not. Without a plan for getting money out efficiently, taxes and timing decide for you.</p></div></div>
    <div class="myth"><span class="mark"></span><div><h3>401ks are easy and high value targets for taxes.</h3><p>Trillions of dollars in tax deferred accounts are a tempting source of revenue. Lawmakers can raise rates or add new rules on these balances with a single bill.</p></div></div>
    <div class="myth"><span class="mark"></span><div><h3>The government can change your 401k and can change the rules at will.</h3><p>Contribution limits, distribution ages and inheritance rules have all changed before. Your plan today may work very differently by the time you retire, and you have no vote.</p></div></div>
    <div class="myth"><span class="mark"></span><div><h3>Turmoil in retirement.</h3><p>When it is time to withdraw, a falling market means selling more shares to cover the same income. Early losses in retirement can shorten how long your savings last by years.</p></div></div>
    <div class="myth"><span class="mark"></span><div><h3>Lost without a comprehensive plan.</h3><p>A 401k is only one piece. Without a plan that ties together taxes, income, insurance and estate goals, your savings work against each other instead of for you.</p></div></div>
    <div class="myth"><span class="mark"></span><div><h3>Neglect of stewardship and responsibility.</h3><p>Handing your future to a plan you do not control is not stewardship. Take an active role, ask hard questions and choose strategies that put your family first. Whatever you choose, we urge you to do it as a conscious decision.</p></div></div>
  </div>
</section>

<section class="suggest">
  <p>We suggest that you don't swallow Wall Street's promises blindly<br>&amp; look to those who tell the whole truth about your financial options.</p>
</section>

<section class="contact-band">
  <h2>Contact us at Sales</h2>
  <div class="contact-lines">
    <span><svg width="30" height="30" viewBox="0 0 24 24"><rect x="2" y="5" width="20" height="14" rx="1" fill="none" stroke="#fff" stroke-width="2"/><path d="M2 6l10 7 10-7" fill="none" stroke="#fff" stroke-width="2"/></svg>Sales@PinegateLark.com</span>
    <span><svg width="28" height="28" viewBox="0 0 24 24"><path fill="#fff" d="M6.6 10.8a15 15 0 0 0 6.6 6.6l2.2-2.2c.3-.3.7-.4 1-.2 1.1.4 2.3.6 3.6.6.6 0 1 .4 1 1V20c0 .6-.4 1-1 1A17 17 0 0 1 3 4c0-.6.4-1 1-1h3.5c.6 0 1 .4 1 1 0 1.3.2 2.5.6 3.6.1.3 0 .7-.2 1z"/></svg>916.555.0142</span>
  </div>
  <p>For a One Hour Look at What Winning the Tax Game Really Looks Like.</p>
</section>

<section class="strategies">
  <h2 class="section-title">Tax Strategies Accountants &amp; Financial Advisors Don't Have</h2>
  <div class="strategy-grid">
    <div class="strategy"><svg width="44" height="44" viewBox="0 0 24 24"><path d="M3 11l9-7 9 7v9H3z" fill="none" stroke="#999" stroke-width="1.6"/><rect x="9" y="14" width="6" height="6" fill="#999"/></svg><h4>Housing Portfolios Against Market Crashes</h4></div>
    <div class="strategy"><svg width="44" height="44" viewBox="0 0 24 24"><circle cx="12" cy="12" r="9" fill="none" stroke="#999" stroke-width="1.6"/><path d="M12 6v12M9 9h5a2 2 0 0 1 0 4h-4a2 2 0 0 0 0 4h5" fill="none" stroke="#999" stroke-width="1.6"/></svg><h4>Seemingly Small Fees Devastate Retirements We Don't Charge Them</h4></div>
    <div class="strategy"><svg width="44" height="44" viewBox="0 0 24 24"><rect x="3" y="8" width="18" height="12" fill="none" stroke="#999" stroke-width="1.6"/><path d="M9 8V5h6v3" fill="none" stroke="#999" stroke-width="1.6"/></svg><h4>Business Owners &amp; Executives Love Our Tax &amp; Bonus Strategies!</h4></div>
    <div class="strategy featured"><svg width="44" height="44" viewBox="0 0 24 24"><path d="M4 20V10M10 20V4M16 20v-7M22 20H2" fill="none" stroke="#fff" stroke-width="1.8"/></svg><h4>401k, Mutual Fund &amp; IRA Myths Revealed</h4></div>
  </div>
</section>

<section class="media">
  <h2 class="section-title">Blogs, Videos &amp; Radio</h2>
  <div class="media-grid">
    <article class="media-card">
      <div class="thumb" role="img" aria-label="Radio station artwork" style="background:linear-gradient(135deg,#f1eef3,#d9d2de)"></div>
      <div class="body"><h4>Heartline Radio</h4><p>Catch us weekly on Heartline Radio's Ron Marsh Radio Hour. Tune in Saturday mornings at 11:00 am for live questions.</p><span class="more">Continue...</span></div>
    </article>
    <article class="media-card">
      <div class="thumb" role="img" aria-label="Advisor speaking on video in an office" style="background:linear-gradient(135deg,#b9b4ae,#5d5853)"></div>
      <div class="body"><h4>PLG Videos</h4><p>Short videos that explain tax strategy, retirement income and common 401k myths in plain language.</p><span class="more">Continue...</span></div>
    </article>
    <article class="media-card">
      <div class="thumb" role="img" aria-label="Banknotes falling through the air" style="background:linear-gradient(135deg,#dcd8c8,#8d8a76)"></div>
      <div class="body"><h4>Money Blog</h4><p>Practical articles on taxes, business owner planning and keeping more of what you have earned.</p><span class="more">Continue...</span></div>
    </article>
  </div>
  <a class="btn">401k Facts</a>
</section>

<section class="testimonials">
  <h2 class="section-title">Testimonials</h2>
  <div class="quote-grid">
    <div class="quote"><div class="avatar" role="img" aria-label="Portrait of client Neal Corbin"></div><h4>Neal Corbin</h4><span class="role">CEO, Valley Trade Association</span><p>Their team showed our members tax strategies our own accountants had never mentioned. Clear, honest and easy to work with. Highly recommended.</p></div>
    <div class="quote"><div class="avatar" role="img" aria-label="Portrait of client Evan Pryor"></div><h4>Evan Pryor</h4><span class="role">Probate Attorney</span><p>I refer clients with confidence. They explain options patiently and build plans that protect families long after retirement begins.</p></div>
    <div class="quote"><div class="avatar" role="img" aria-label="Portrait of client Marc Lindell"></div><h4>Marc Lindell</h4><span class="role">Doctor</span><p>As a busy physician I needed straight answers. They found savings I had missed for years. I only wish I had called them sooner.</p></div>
  </div>
  <div class="subscribe"><span class="field">Shoot us a quick email here</span><span class="go">Submit</span></div>
</section>

<footer class="site-footer">
  <div class="wrap">
    <div class="footer-grid">
      <div class="footer-col footer-about">
        <div class="brand"><span class="brand-dot"></span><span class="brand-name">Pinegate Lark Group</span></div>
        <p>Pinegate Lark Group brings sensibility, predictability and peace of mind to retirement. We will bring you the financial tools accountants and Wall Street advisors never share.</p>
      </div>
      <div class="footer-col">
        <h4>Quick Link</h4>
        <ul class="links"><li>Home</li><li>About us</li><li>Seminars</li><li>Blogs</li><li>Testimonials</li><li>Contact us</li></ul>
      </div>
      <div class="footer-col">
        <h4>Address</h4>
        <ul class="address">
          <li><svg width="14" height="14" viewBox="0 0 24 24"><path fill="#e53238" d="M12 2a7 7 0 0 0-7 7c0 5 7 13 7 13s7-8 7-13a7 7 0 0 0-7-7zm0 9.5A2.5 2.5 0 1 1 12 6.5a2.5 2.5 0 0 1 0 5z"/></svg><span>2210 Alder Crest Way,<br>Oakmere,<br>CA 95000</span></li>
          <li><svg width="14" height="14" viewBox="0 0 24 24"><path fill="#e53238" d="M6.6 10.8a15 15 0 0 0 6.6 6.6l2.2-2.2c.3-.3.7-.4 1-.2 1.1.4 2.3.6 3.6.6.6 0 1 .4 1 1V20c0 .6-.4 1-1 1A17 17 0 0 1 3 4c0-.6.4-1 1-1h3.5c.6 0 1 .4 1 1 0 1.3.2 2.5.6 3.6.1.3 0 .7-.2 1z"/></svg><span>916.555.0142</span></li>
          <li><svg width="14" height="14" viewBox="0 0 24 24"><rect x="2" y="5" width="20" height="14" fill="none" stroke="#e53238" stroke-width="2"/><path d="M2 6l10 7 10-7" fill="none" stroke="#e53238" stroke-width="2"/></svg><span>Sales@PinegateLark.com</span></li>
        </ul>
      </div>
      <div class="footer-col footer-form">
        <h4>Contact us</h4>
        <div class="row"><span>Name</span><span>Email</span><span>Phone</span></div>
        <div class="msg">Message</div>
        <span class="footer-btn">Baby Boomer Edition</span>
      </div>
    </div>
  </div>
  <div class="copyright"><div class="wrap"><span>Copyright © 2019 Pinegate Lark Group. All Right Reserve</span><span>Privacy · Terms</span></div></div>
</footer>

</body>
</html>
```